Brell Stone Company Business Cards

Front and Back Business Card - logo and text setup - cool design. I need workable photoshop or illustrator files so I can setup each employee card with design that is created
Updates

Hi everyone, thank you for the great entries. Please no more white and blue cards - there are so many already - black and silver only now please. thanks!

Target Market(s)

Construction Industry - Facility Managers

Industry/Entity Type

Construction

Contact Information for Business Card

I really like contemporary simplistic looks - clean neat....not opposed to seeing some black backrounds

Requirements
Must have
• Logo/website address with design on front only - www.brellstone-example.com (logo attached)
• Back:
• Name/Title/Company Address/Phone/email address
Nice to have
• Cool design
Should not have
• Nothing gimmicky like Fire or Water - since we are a Fire Protection company - it has all been done

```html
<!DOCTYPE html>
<html lang="en">
<head>
<meta charset="utf-8">
<title>Brell Stone Company Business Cards</title>
<link rel="stylesheet" href="https://fonts.googleapis.com/css2?family=Lato:wght@400;700;900&display=swap">
<style>
  :root {
    --backdrop: #2a2a2c;
    --card-silver: #e4e5e7;
    --card-silver-deep: #c9cbce;
    --card-black: #141415;
    --ink-black: #1b1b1d;
    --ink-steel: #6e7177;
    --text-grey: #3e3f42;
    --rule-silver: #a3a6ab;
    --silver-bright: #d2d4d8;
  }
  * { box-sizing: border-box; margin: 0; padding: 0; }
  html, body {
    width: 1200px; height: 1108px; overflow: hidden;
    background: var(--backdrop);
    font-family: "Lato", sans-serif;
  }
  .stage {
    position: relative; width: 1200px; height: 1108px;
    display: flex; justify-content: center; align-items: center; gap: 80px;
  }
  .card {
    position: relative; width: 370px; height: 620px;
    border-radius: 26px; overflow: hidden;
    box-shadow: 0 18px 40px rgba(0,0,0,.45);
  }
  .card--front {
    background: linear-gradient(160deg, var(--card-silver) 0%, #f1f2f3 45%, var(--card-silver-deep) 100%);
  }
  .card--back { background: var(--card-black); }

  .wordmark {
    position: absolute; left: 40px; top: 110px; width: 290px;
    font-weight: 900; font-size: 48px; line-height: 1; color: var(--ink-black);
    text-align: center; letter-spacing: -0.5px;
  }
  .wordmark__badge {
    display: block; width: 22px; height: 22px; margin: 14px auto 0;
    background: var(--ink-steel);
  }

  .person { position: absolute; left: 0; right: 0; top: 330px; text-align: center; }
  .person__name {
    font-size: 25px; font-weight: 400; color: var(--ink-black); letter-spacing: 0.3px;
  }
  .person__name .surname { color: var(--ink-steel); }
  .person__title { font-size: 17px; color: var(--text-grey); margin-top: 4px; }

  .icon-rule {
    position: absolute; left: 50px; right: 50px; top: 412px;
    display: flex; align-items: center; gap: 8px;
  }
  .icon-rule__line { flex: 1; height: 1.5px; background: var(--rule-silver); }
  .icon-rule__icons { display: flex; gap: 5px; }
  .icon-rule__icons svg { width: 26px; height: 26px; display: block; }

  .contact {
    position: absolute; left: 0; right: 0; top: 452px; text-align: center;
    font-size: 17px; line-height: 26px; color: var(--text-grey);
  }
  .contact__rule {
    position: absolute; left: 70px; right: 70px; top: 540px;
    height: 1.5px; background: var(--rule-silver);
  }
  .address {
    position: absolute; left: 0; right: 0; top: 552px; text-align: center;
    font-size: 17px; line-height: 25px; color: var(--text-grey);
  }

  .back-wordmark {
    position: absolute; left: 36px; bottom: 118px;
    font-weight: 900; font-size: 50px; line-height: 1; color: var(--silver-bright);
    display: flex; align-items: center; gap: 12px; letter-spacing: -0.5px;
  }
  .back-wordmark__badge { width: 18px; height: 18px; background: var(--silver-bright); }
  .back-url {
    position: absolute; left: 36px; bottom: 70px;
    font-size: 19px; color: var(--silver-bright);
  }
</style>
</head>
<body>
<main class="stage">
  <section class="card card--front" aria-label="Card front">
    <div class="wordmark">Brell Stone<span class="wordmark__badge"></span></div>

    <div class="person">
      <p class="person__name">MARCUS <span class="surname">HALE</span></p>
      <p class="person__title">Managing Director</p>
    </div>

    <div class="icon-rule">
      <span class="icon-rule__line"></span>
      <span class="icon-rule__icons">
        <svg viewBox="0 0 26 26" aria-label="Phone">
          <circle cx="13" cy="13" r="13" fill="#1b1b1d"/>
          <path d="M9 7.5l2.2-.5 1.2 3-1.4 1a7 7 0 0 0 3.5 3.5l1-1.4 3 1.2-.5 2.2c-5 .3-9.3-4-9-9z" fill="#e4e5e7"/>
        </svg>
        <svg viewBox="0 0 26 26" aria-label="Email">
          <circle cx="13" cy="13" r="13" fill="#1b1b1d"/>
          <rect x="7" y="9" width="12" height="8.5" fill="#e4e5e7"/>
          <polyline points="7,9 13,14 19,9" fill="none" stroke="#1b1b1d" stroke-width="1.3"/>
        </svg>
        <svg viewBox="0 0 26 26" aria-label="Website">
          <circle cx="13" cy="13" r="13" fill="#1b1b1d"/>
          <circle cx="13" cy="13" r="6" fill="none" stroke="#e4e5e7" stroke-width="1.4"/>
          <ellipse cx="13" cy="13" rx="2.6" ry="6" fill="none" stroke="#e4e5e7" stroke-width="1.2"/>
          <line x1="7" y1="13" x2="19" y2="13" stroke="#e4e5e7" stroke-width="1.2"/>
        </svg>
      </span>
      <span class="icon-rule__line"></span>
    </div>

    <div class="contact">
      <p>044-987 654 321</p>
      <p>info@brellstone-example.com</p>
      <p>www.brellstone-example.com</p>
    </div>
    <div class="contact__rule"></div>
    <div class="address">
      <p>88, Granite Road,</p>
      <p>45710, Northland</p>
    </div>
  </section>

  <section class="card card--back" aria-label="Card back">
    <div class="back-wordmark">Brell Stone<span class="back-wordmark__badge"></span></div>
    <p class="back-url">www.brellstone-example.com</p>
  </section>
</main>
</body>
</html>
```